Hong Kong based International Remittance and ForEx company requires website design

We need a website designed for a new European - Hong Kong based ForEx & fund remittence entity.

The company specialises in larger corporate & high net worth private client trades, therefore the design must aesthetically reflect this (sophisticated). As a theme colour, financial entities tend to use either blue or red; if blue, our preference is a darker blue. Visually, our preference is less copy, more imagery.

Number of pages would be limited; landing (home), about us, client registration (x1 Corporate form, x1 Private Client form), Contact Us.

Have uploaded the existing logo - please note this is to be redesigned, although the colour scheme will remain the same. Please also note that copy will follow - please use Lorem Ipsum.

Target Market(s)

Medium to large Corporations. High net worth individuals.

Industry/Entity Type

Financial Service

Coding

Coded - Design and coding required

Number of Pages Required

4 page

Font styles to use
Serif

Requirements
Nice to have
• ForEx ticker,

```html
<!DOCTYPE html>
<html lang="en">
<head>
<meta charset="utf-8">
<title>Harbourline Incorporation — Home</title>
<link href="https://fonts.googleapis.com/css2?family=Open+Sans:wght@400;600;700&display=swap" rel="stylesheet">
<style>
:root{
  --navy:#1b3a73;
  --navy-deep:#17346e;
  --red:#c8161d;
  --up:#1f8a2c;
  --down:#d0161d;
  --text:#555;
  --rule:#d8d8d8;
  --footer:#2b2b2b;
  --footer-base:#222;
  --footer-text:#c9c9c9;
  --white:#fff;
}
*{box-sizing:border-box;margin:0;padding:0}
html,body{width:977px;height:1200px;overflow:hidden;background:var(--white)}
body{font-family:"Open Sans",Arial,sans-serif;color:var(--text);position:relative}
.abs{position:absolute}

/* ticker */
.ticker{top:0;left:0;width:977px;height:28px;background:#f3f3f3;border-bottom:1px solid #e2e2e2}
.ticker-label{left:107px;top:0;width:125px;height:28px;background:var(--red);color:var(--white);font-size:10px;line-height:28px;text-align:center}
.ticker-items{left:251px;top:0;height:28px;display:flex;gap:12px;font-size:9.5px;line-height:28px;color:var(--navy)}
.ticker-items .dn{color:var(--down)}
.ticker-items .up{color:var(--up)}
.ticker-items i{font-style:normal;font-size:7px}

/* header */
.brand{left:107px;top:62px}
.brand-name{font-size:30px;font-weight:400;color:#1a1a1a;letter-spacing:-0.5px;line-height:1;display:flex;align-items:center;gap:8px}
.brand-mark{width:12px;height:12px;border-radius:50%;background:var(--navy)}
.brand-sub{font-size:7px;letter-spacing:2.6px;color:#333;margin-top:5px}
.search{left:554px;top:47px;width:145px;height:27px;display:flex}
.search-input{flex:1;border:1px solid #ccc;font-size:9.5px;color:#777;padding:0 10px;line-height:25px}
.search-btn{width:29px;background:var(--navy-deep);display:flex;align-items:center;justify-content:center}
.lang{left:710px;top:47px;width:72px;height:27px;border:1px solid #ccc;background:#f6f6f6;font-size:9.5px;color:#555;display:flex;align-items:center;gap:5px;padding-left:8px}
.lang .flag{width:11px;height:7px;background:#3a4d8f}
.region-map{left:804px;top:35px;width:62px;height:47px;background:linear-gradient(135deg,#b8b8b8,#8f8f8f);border-radius:40% 55% 45% 50%}
.nav{left:318px;top:95px;display:flex;gap:0;font-size:9.5px;color:#444}
.nav a{text-decoration:none;color:inherit;margin-right:19px}
.nav a.active{color:var(--navy)}
.nav-underline{left:314px;top:123px;width:38px;height:3px;background:var(--navy)}

/* hero */
.hero{left:0;top:125px;width:977px;height:333px;background:radial-gradient(ellipse at 55% 40%,#3a3f8f 0%,#1c1c3a 45%,#0c0d18 80%),#0d0d1a}
.hero-glow{left:600px;top:125px;width:377px;height:333px;background:linear-gradient(160deg,rgba(220,210,40,.0) 30%,rgba(200,200,30,.55) 80%)}
.hero-title{left:107px;top:229px;font-size:24px;font-weight:700;color:var(--white);line-height:29px}
.btn-details{left:107px;top:310px;width:81px;height:31px;background:var(--red);color:var(--white);font-size:9px;font-weight:700;line-height:31px;text-align:center;border-radius:2px}
.dots{left:107px;top:365px;display:flex;gap:9px}
.dots span{width:4px;height:4px;border-radius:50%;background:#999}
.dots span:first-child{background:var(--white)}
.converter{left:633px;top:206px;width:237px;height:146px;background:var(--navy-deep)}
.field{position:absolute;height:27px;background:var(--white);font-size:8.5px;color:#444;line-height:27px;padding-left:8px}
.field::after{content:"";position:absolute;right:10px;top:10px;width:4px;height:4px;border-right:1px solid #666;border-bottom:1px solid #666;transform:rotate(45deg)}
.result{left:17px;top:95px;font-size:8.5px;color:#dce3f0;line-height:17px}

/* services */
.service{top:498px;width:225px}
.service-photo{width:225px;height:125px;border:3px solid var(--white);box-shadow:0 0 0 1px #ddd}
.service h3{margin-top:25px;font-size:12px;font-weight:700;color:var(--navy);letter-spacing:.2px}
.service p{margin-top:8px;font-size:8.5px;line-height:16px;color:var(--text);padding-left:1px}
.more{display:block;margin-top:6px;font-size:8.5px;color:var(--navy);padding-left:1px}
.divider{left:107px;top:749px;width:763px;height:1px;background:var(--rule)}

/* news */
.news-heading{left:107px;top:772px;font-size:12px;font-weight:700;color:var(--navy)}
.news{top:816px;display:flex;gap:18px}
.news-photo{width:125px;height:104px}
.news-body h4{font-size:11.5px;font-weight:700;color:var(--navy);line-height:14px;width:215px}
.news-body .date{margin-top:9px;font-size:8.5px;color:#555}
.news-body p{margin-top:11px;font-size:8.5px;line-height:16px;color:var(--text);padding-left:2px}
.news-body .more{margin-top:6px}

/* footer */
.footer{left:0;top:962px;width:977px;height:195px;background:var(--footer)}
.footer-col{top:986px}
.footer-col h5{font-size:11px;font-weight:600;color:var(--white);margin-bottom:8px}
.footer-col ul{list-style:none}
.footer-col li{font-size:9.5px;color:var(--footer-text);line-height:19.5px;padding-left:13px;position:relative}
.footer-col li::before{content:"";position:absolute;left:1px;top:6px;border-left:4px solid var(--white);border-top:3px solid transparent;border-bottom:3px solid transparent}
.base{left:0;top:1157px;width:977px;height:43px;background:var(--footer-base)}
.copyright{left:108px;top:1172px;font-size:9.5px;color:var(--footer-text)}
.social{left:792px;top:1174px;display:flex;gap:12px}
.social span{width:10px;height:10px;border-radius:50%;background:#cfcfcf}
</style>
</head>
<body>

<div class="abs ticker"></div>
<div class="abs ticker-label">Live Forex Rates Ticker</div>
<div class="abs ticker-items">
  <span>USDJPY = <b class="dn" style="font-weight:400">112.9825</b> <i class="dn">▼</i></span>
  <span>USDCAD = <b class="up" style="font-weight:400">1.35583</b> <i class="up">▲</i></span>
  <span>AUDCAD = <b class="dn" style="font-weight:400">0.96889</b> <i class="dn">▼</i></span>
  <span>EURGBP = <b class="up" style="font-weight:400">0.78624</b> <i class="up">▲</i></span>
  <span>NZDUSD = <b class="dn" style="font-weight:400">0.65905</b> <i class="dn">▼</i></span>
  <span>USDCNY = <b class="up" style="font-weight:400">6.5531</b> <i class="up">▲</i></span>
  <span>EURJPY = <b class="dn" style="font-weight:400">123.07297</b> <i class="dn">▼</i></span>
</div>

<header>
  <div class="abs brand">
    <div class="brand-name">Harbourline <span class="brand-mark"></span></div>
    <div class="brand-sub">INCORPORATION LIMITED</div>
  </div>
  <div class="abs search">
    <div class="search-input">Search</div>
    <div class="search-btn">
      <svg width="10" height="10" viewBox="0 0 10 10"><circle cx="4" cy="4" r="3" fill="none" stroke="#fff" stroke-width="1.5"/><line x1="6.2" y1="6.2" x2="9" y2="9" stroke="#fff" stroke-width="1.6"/></svg>
    </div>
  </div>
  <div class="abs lang"><span class="flag"></span>English <span style="font-size:7px">▼</span></div>
  <div class="abs region-map" role="img" aria-label="Map outline of Hong Kong"></div>
  <nav class="abs nav">
    <a class="active">HOME</a><a>ABOUT US</a><a>INTERNATIONAL PAYMENTS</a><a>INTERNATIONAL PAYMENTS</a><a>CLIENT APPLICATION</a><a style="margin-right:0">CONTAT US</a>
  </nav>
  <div class="abs nav-underline"></div>
</header>

<section>
  <div class="abs hero" role="img" aria-label="Illuminated forex rate board with currency figures and a rising red chart line"></div>
  <div class="abs hero-glow"></div>
  <h1 class="abs hero-title">PRACTICING IN THE<br>FOREX MARKET</h1>
  <div class="abs btn-details">VIEW DETAILS</div>
  <div class="abs dots"><span></span><span></span><span></span></div>
  <div class="abs converter">
    <div class="field" style="left:18px;top:23px;width:65px">100</div>
    <div class="field" style="left:93px;top:23px;width:127px;padding-left:15px">British Pound Sterling</div>
    <div class="field" style="left:18px;top:59px;width:65px">1078.73</div>
    <div class="field" style="left:93px;top:59px;width:127px;padding-left:15px">Hongkong Dollar</div>
    <div class="abs result">100.00 British Pound Sterling is<br>1,079.560 Hong Kong Dollar</div>
  </div>
</section>

<section>
  <article class="abs service" style="left:107px">
    <div class="service-photo" role="img" aria-label="Golden coins and currency symbols" style="background:linear-gradient(135deg,#e0701c,#f6b233 55%,#f3c24a)"></div>
    <h3>INTERNATIONAL MONEY TRANSFER</h3>
    <p>We provide the international settlement and reconcilia-<br>tion of funds for and on behalf</p>
    <a class="more">Read More &gt;&gt;</a>
  </article>
  <article class="abs service" style="left:376px">
    <div class="service-photo" role="img" aria-label="Hands holding a phone with glowing global network" style="background:radial-gradient(circle at 55% 45%,#6fd0d8 0%,#2a5b7a 25%,#141522 65%)"></div>
    <h3>FOREIGN EXCHANGE</h3>
    <p>We provide the international settlement and reconcilia-<br>tion of funds for and on behalf</p>
    <a class="more">Read More &gt;&gt;</a>
  </article>
  <article class="abs service" style="left:647px">
    <div class="service-photo" role="img" aria-label="Business people in a bright office beside a desk" style="background:linear-gradient(180deg,#9cb6c6,#dfe7ec 60%,#f1efe9)"></div>
    <h3>PAYING &amp; RECEIVING AGENCY</h3>
    <p>We provide the international settlement and reconcilia-<br>tion of funds for and on behalf</p>
    <a class="more">Read More &gt;&gt;</a>
  </article>
</section>

<div class="abs divider"></div>

<section>
  <h2 class="abs news-heading">RECENT NEWS</h2>
  <article class="abs news" style="left:107px">
    <div class="news-photo" role="img" aria-label="Businessman viewing a glowing market chart" style="background:linear-gradient(135deg,#1d4a66,#4d90a8 50%,#c94a2e)"></div>
    <div class="news-body">
      <h4>FOREX TRADING- ARE YOU GAINING OR LOSING?</h4>
      <div class="date">FEB29,2015</div>
      <p>We provide the international settlement and recon-<br>ciliation of funds for and on behalf</p>
      <a class="more">Read More &gt;&gt;</a>
    </div>
  </article>
  <article class="abs news" style="left:518px">
    <div class="news-photo" role="img" aria-label="Close-up of a digital forex rate display" style="background:linear-gradient(135deg,#0c2c8c,#2a5ad0 45%,#c21d2c)"></div>
    <div class="news-body">
      <h4>FOREX TRADING- ARE YOU GAINING OR LOSING?</h4>
      <div class="date">FEB29,2015</div>
      <p>We provide the international settlement and recon-<br>ciliation of funds for and on behalf</p>
      <a class="more">Read More &gt;&gt;</a>
    </div>
  </article>
</section>

<footer>
  <div class="abs footer"></div>
  <div class="abs footer-col" style="left:109px"><h5>ABOUT US</h5><ul><li>Our Ethos</li><li>Affiliates</li><li>FAQ's</li></ul></div>
  <div class="abs footer-col" style="left:274px"><h5>INTERNATIONAL PAYMENTS</h5><ul><li>Making Payments</li><li>Customer Protection</li><li>NoObligation</li><li>Corporate Clients</li><li>Private Clients</li></ul></div>
  <div class="abs footer-col" style="left:519px"><h5>CLIENT APPLICATION</h5><ul><li>Private Client</li><li>Corporate Client</li></ul></div>
  <div class="abs footer-col" style="left:746px"><h5>COMPANY</h5><ul><li>Terms&amp;Conditions</li><li>Peace of Mind</li><li>Data Protection&amp;Privacy</li><li>AntiMoneyLaundering</li><li>Legal</li><li>Contact Us</li></ul></div>
  <div class="abs base"></div>
  <div class="abs copyright">© 2016 Harbourline Incorporation</div>
  <div class="abs social"><span></span><span></span><span></span><span></span></div>
</footer>

</body>
</html>
```